New Business Card

Need new business cards like attached. if possible add QR code. Vertical Business Card

I need creative and unique business card design using my company logo. Ok to change logo color. We are a small brokerage doing both Real Estate and Mortgage services. Need to have the follow on business card;
1. agent name - Nola Brenner - Realtor
2. cell - 555-555-2146
3. license number - DRE 07461392
4. business name - Tallow Ridge Realty & Lending, Inc
5. business office - 555-555-4817
6. business address - 482 W. Larkmoor Ave #212, Fenmoor Vale ZZ 00000
7. business logo - attached (ok to use different color on logo)

```html
<!DOCTYPE html>
<html lang="en">
<head>
<meta charset="utf-8">
<title>Tallow Ridge Realty &amp; Lending – Business Card</title>
<link href="https://fonts.googleapis.com/css2?family=Montserrat:wght@400;500;700;800&display=swap" rel="stylesheet">
<style>
  :root {
    --stage: #e6e7ea;
    --card-white: #f7f7f7;
    --card-black: #15161a;
    --brand-blue: #1e3fa8;
    --brand-sky: #2a8be8;
    --ink: #2a2a2e;
  }
  * { box-sizing: border-box; margin: 0; padding: 0; }
  html, body { width: 1200px; height: 800px; overflow: hidden; }
  body {
    background: var(--stage);
    font-family: "Montserrat", sans-serif;
    position: relative;
  }
  .card {
    position: absolute;
    top: 120px;
    width: 320px;
    height: 560px;
    border-radius: 22px;
    overflow: hidden;
    box-shadow: 0 10px 30px rgba(0,0,0,.18);
  }
  .card-back {
    left: 250px;
    background: var(--card-black);
  }
  .back-pattern {
    position: absolute;
    inset: 0;
    background: linear-gradient(160deg, #3a3b40 0%, #1d1e22 45%, #0e0f12 100%);
  }
  .back-mark {
    position: absolute;
    left: 50%;
    top: 62%;
    transform: translateX(-50%);
    display: flex;
    align-items: center;
    gap: 8px;
    color: var(--brand-sky);
    font-weight: 700;
    font-size: 13px;
    letter-spacing: .04em;
    white-space: nowrap;
  }
  .mark-square {
    width: 14px; height: 14px;
    background: var(--brand-sky);
  }
  .card-front {
    left: 630px;
    background: var(--card-white);
    text-align: center;
    padding: 70px 22px 0;
  }
  .brand {
    display: flex;
    flex-direction: column;
    align-items: center;
    gap: 16px;
  }
  .brand-square {
    width: 84px; height: 84px;
    background: var(--brand-blue);
  }
  .brand-name {
    color: var(--brand-blue);
    font-weight: 500;
    font-size: 15px;
    letter-spacing: .16em;
    text-transform: uppercase;
    line-height: 1.5;
  }
  .agent-name {
    margin-top: 46px;
    color: var(--brand-blue);
    font-weight: 800;
    font-size: 26px;
    letter-spacing: -.01em;
    text-transform: uppercase;
  }
  .agent-role {
    color: var(--ink);
    font-weight: 500;
    font-size: 20px;
    margin-top: 2px;
  }
  .contact {
    margin-top: 22px;
    font-size: 15px;
    line-height: 1.55;
    color: var(--ink);
  }
  .contact .label { color: var(--brand-sky); }
  .office {
    margin-top: 14px;
    font-size: 14px;
    line-height: 1.5;
    color: var(--ink);
  }
  .office .company { color: var(--brand-blue); font-weight: 500; }
  .license {
    margin-top: 12px;
    font-size: 14px;
    color: var(--ink);
  }
</style>
</head>
<body>
  <section class="card card-back">
    <div class="back-pattern" role="img" aria-label="Dark embossed repeating brand pattern on black card stock"></div>
    <div class="back-mark"><span class="mark-square"></span>Tallow Ridge</div>
  </section>

  <section class="card card-front">
    <header class="brand">
      <span class="brand-square"></span>
      <p class="brand-name">Tallow Ridge Realty<br>&amp; Lending, Inc</p>
    </header>
    <h1 class="agent-name">Nola Brenner</h1>
    <p class="agent-role">Realtor</p>
    <p class="contact">
      <span class="label">M :</span> 555-555-2146<br>
      <span class="label">T :</span> 555-555-4817
    </p>
    <p class="office">
      <span class="company">Tallow Ridge Realty &amp; Lending, Inc</span><br>
      482 W. Larkmoor Ave #212,<br>
      Fenmoor Vale ZZ 00000
    </p>
    <p class="license">LIC : DRE 07461392</p>
  </section>
</body>
</html>
```